Biz Card Design TVCP

New business card for a new company.
Logo was completed by a designer on ArtHarbor and looking to continue requesting additional services.
Company Name: Tidal Vector Power Consulting
Although this company is starting in Canada, we will be moving towards a global presence within the next 6 months.
Key elements to this business are as follows.
Energy Procurement
Energy Reduction Services
Demand Side Consulting
Energy Efficiency Consulting
Saving Clients Money
Helping Them Go "Green"
Managing Their Energy Requirements
Basically the goal for our company is to find the best procurement solution for our clients and reduce their energy consumption. This reduces their expenses and the amount of greenhouse gas they produce on a daily basis.
I have been in the energy footprint for the last 20 years and know that most companies are looking to "do whatever is necessary to get them to sign on the dotted line". I would prefer to walk away from a client that I can't help than to put them into a situation that they will regret for years to come. This is where the "TIDAL" part of the company name comes from.
The following is a catch phrase that encompasses what we do.
"Reducing your carbon footprint & energy bill at the same time!"
The back of the card needs to have this statement along with some sort of illustration. The back is a playground for creative ideas.
The front of the card needs the following.
Logo.
First & Last Name (Gus Marwick)
Title (Energy Warrior)
Phone Number (555) 314-2718
Fax Number (555) 271-8314
Email Address gus@tidalvectorpowerconsulting.example
Address 47 fenwick rd Toronto Ontario K4T 2P9
I want it to be a card that is remembered when any of my staff give it to a customer. It HAS to stand out.
Target Market(s)
Business Owners, Decision Makers, 30 to 65+
Industry/Entity Type
Business
Look and feel

```html
<!DOCTYPE html>
<html lang="en">
<head>
<meta charset="utf-8">
<title>Tidal Vector Power Consulting – Business Card</title>
<link rel="stylesheet" href="https://fonts.googleapis.com/css2?family=Nunito:wght@300;800&family=Tinos&display=swap">
<style>
  :root {
    --leaf-light: #c9e28c;
    --leaf-mid: #5fb05a;
    --leaf-deep: #07853f;
    --edge-blue: #3f6db8;
    --ink: #111111;
    --paper: #ffffff;
  }
  html, body {
    margin: 0;
    padding: 0;
    overflow: hidden;
    background: var(--paper);
  }
  .card {
    position: relative;
    width: 1200px;
    height: 686px;
    overflow: hidden;
    background: var(--paper);
  }
  .card__shape {
    position: absolute;
    inset: 0;
    width: 1200px;
    height: 686px;
  }
  .identity {
    position: absolute;
    left: 41px;
    top: 100px;
    color: var(--paper);
  }
  .identity__name {
    margin: 0;
    font-family: "Nunito", sans-serif;
    font-weight: 800;
    font-size: 51px;
    line-height: 1;
    letter-spacing: -0.5px;
  }
  .identity__title {
    margin: 8px 0 0 2px;
    font-family: "Nunito", sans-serif;
    font-weight: 300;
    font-size: 33px;
    line-height: 1;
    letter-spacing: 0.5px;
  }
  .brand {
    position: absolute;
    right: 42px;
    top: 158px;
    margin: 0;
    font-family: "Nunito", sans-serif;
    font-weight: 800;
    font-size: 33px;
    line-height: 1;
    color: var(--edge-blue);
    letter-spacing: -0.3px;
  }
  .contact {
    position: absolute;
    right: 40px;
    top: 480px;
    margin: 0;
    font-family: "Tinos", serif;
    font-style: normal;
    font-size: 25px;
    line-height: 34.5px;
    text-align: right;
    color: var(--ink);
  }
  .contact__label {
    color: var(--edge-blue);
  }
</style>
</head>
<body>
  <div class="card">
    <svg class="card__shape" viewBox="0 0 1050 600" preserveAspectRatio="none" aria-hidden="true">
      <defs>
        <linearGradient id="leaf-field" x1="0" y1="0" x2="1" y2="1">
          <stop offset="0" stop-color="var(--leaf-light)"/>
          <stop offset="0.45" stop-color="var(--leaf-mid)"/>
          <stop offset="1" stop-color="var(--leaf-deep)"/>
        </linearGradient>
      </defs>
      <path class="edge-band" fill="var(--edge-blue)"
        d="M0,0 H493 C512,90 552,160 602,205 C670,265 765,330 845,375 C712,402 545,470 412,600 H0 Z"/>
      <path class="field" fill="url(#leaf-field)"
        d="M0,0 H478 C498,90 540,160 590,205 C660,265 760,330 845,375 C700,388 520,452 390,600 H0 Z"/>
    </svg>

    <header class="identity">
      <h1 class="identity__name">Gus Marwick</h1>
      <p class="identity__title">Energy Warrior</p>
    </header>

    <p class="brand">Tidal Vector Power Consulting</p>

    <address class="contact">
      47 fenwick rd Toronto Ontario<br>
      K4T 2P9<br>
      <span class="contact__label">Ph:</span> (555) 314-2718<br>
      <span class="contact__label">Fax:</span> (555) 271-8314<br>
      <span class="contact__label">Email:</span> gus@tidalvectorpowerconsulting.example
    </address>
  </div>
</body>
</html>
```